Logo and Website Design for QR.KA Horizon - a Software Engineering and IT company

Software engineering and IT are two different disciplines - and yet inseparably linked. At QR.KA Horizon, we combine both worlds and ensure that our software solutions are not only innovative and powerful, but also integrate perfectly into existing IT landscapes. Vision stands more for imagination, so it is not neccessary something what has to do with visualisation. Please consider that the winning competitor is also instructed to make a logo for the company. So please make a suitable logo for QR.KA Horizon to which the website fits to and show it during the website creation process. A good Logo desing is important for winning the competition. The website should contain a landing page with inspiring, perhaps futuristic photos of a datacenter and lines of code. Eventuelly flewent integrated in the text. On the landing page the company should introduced with a small text (max 250 words) followed by a section with a short text to one of our products nearby a graphic visualising the architecture of the product. The menue should be on top and fixed during scrolling and consist of the menue items home, solutions, who are we and a contact button. There should be a footer for linking social media, rights and Impressum. Only as an idea not a must. The very first view on the landing page could also be the menue bar and below of it a transparent unsharp photo (e.g. datacenter, lines of code, both ;) with the company name in the center.

###############################################################

Hi Designers,

Despite your very good approaches for describing QR.KA Horizon, here a short introduction (german text) from ourself:

------
QR.KA Horizon – Ihr Partner für ganzheitliche Softwarelösungen

Die QR.KA Horizon ist ein dynamisches Unternehmen, das sich nicht nur auf die Konzeption, das Design und die Entwicklung maßgeschneiderter Software spezialisiert hat, sondern auch deren reibungslosen Betrieb sicherstellt. Mit einem Team aus erfahrenen Softwarearchitekten und IT-Professionals verbinden wir modernste Softwareentwicklung mit tiefgehendem IT-Know-how – für Lösungen, die nachhaltig, leistungsstark und zukunftssicher sind.

Software Engineering trifft IT – Perfektion in Kombination
Software Engineering und IT sind zwei unterschiedliche Disziplinen – und doch untrennbar miteinander verbunden. Wir bei QR.KA Horizon vereinen beide Welten und sorgen dafür, dass unsere Softwarelösungen nicht nur innovativ und leistungsfähig sind, sondern sich auch perfekt in bestehende IT-Landschaften integrieren.

Expertise mit Fokus auf Healthcare & komplexe IT-Umgebungen
Unsere Experten bringen jahrzehntelange Erfahrung aus dem Healthcare-Sektor mit und unterstützen IT-Abteilungen großer Kliniken in der Entwicklung und Optimierung von Softwarelösungen. Von Anwendungssoftware bis hin zu Steuerungssystemen – unsere Softwareingenieure wissen genau, worauf es ankommt.

Ganzheitlicher Ansatz – über die Software hinaus
Wir entwickeln nicht nur Software, sondern übernehmen auch die Verantwortung für deren stabile und effiziente Betriebsumgebung. Egal, ob on-premises, in der Cloud oder als SaaS-Lösung – wir kümmern uns um den kompletten Lifecycle Ihrer Anwendung.

Ihre Vision – unsere Mission.
Ob Neuentwicklung einer SaaS-Anwendung oder die Migration bestehender Lösungen in eine moderne SaaS-Umgebung – mit QR.KA Horizon haben Sie einen starken Partner an Ihrer Seite.

Lassen Sie uns gemeinsam die Zukunft Ihrer Software gestalten!
--------------

Our first solution called "Clear Record Transfer Gateway" (CLURA)
-------------------
Teilen Sie Ihre Daten sicher – ohne Kompromisse!

Sie nutzen eine relationale Datenbank (Brightcask, Tabulon Hub, Vellumdb etc.) und möchten ausgewählte Daten mit Dritten teilen – sei es für ein Data Warehouse, Business Controller, Lieferanten oder Kunden? Doch dabei sollen Datensicherheit, Integrität und Verfügbarkeit Ihrer primären Lösung in keiner Weise gefährdet werden?

Mit unserer Lösung erhalten Sie genau das: Maximalen Schutz für Ihre Anwendung bei gleichzeitigem Nutzen durch autorisierte Dritte – ganz ohne teure Lizenzkosten für eine Schattendatenbank.

Lassen Sie uns gemeinsam herausfinden, wie Sie Ihre Daten sicher und effizient nutzen können. Kontaktieren Sie uns – wir zeigen Ihnen, was möglich ist!
---------------------

Our second solution MIVO:
---------------------
MIVO – Program for a Tone Matching Instrument ist die smarte Lösung für Unternehmen, die bei Farbgenauigkeit keine Kompromisse machen. Die Software erkennt Farbabweichungen zwischen Mustern vollautomatisch, beschreibt sie verständlich und sorgt so für gleichbleibend hohe Produktqualität – schnell, visuell und präzise. Perfekt für alle, die Farbe zur Vertrauenssache machen.
-------------------------

Thanks,
Gerold

Target Market(s)

IT Professionals from any sector

Industry/Entity Type

Healthcare and other

Coding

Coded - Design and coding required

Number of Pages Required

1 page

Font styles to use
Sans Serif

Colors
0054AA
0677BA
7BADD7
CADEEF
E8F1F8
0094D4
00A9DD
6FCCEA
C7EBF8
E9F6FB
00AB8E
00BBA5
67D7C9
C6EFE9
E9F9F6

Requirements
Must have
• Please see description
Nice to have
• On the landing page the company should introduced with a small text (max 250 words) followed by a section with a short text to one of our products nearby a graphic visualising the architecture of the product. The menue should be on top and fixed during scrolling and consist of the menue items home, solutions, who are we and a contact button. There should be a footer for linking social media, rights and Impressum. Only as an idea not a must. The very first view on the landing page could also be the menue bar and below of it a transparent unsharp photo (e.g. datacenter, lines of code, both ;) with the company name in the center.
Should not have
• Please see description

```html
<!DOCTYPE html>
<html lang="en">
<head>
<meta charset="utf-8">
<title>QR.KA Horizon – Software Engineering &amp; IT</title>
<link rel="stylesheet" href="https://fonts.googleapis.com/css2?family=Montserrat:wght@400;500;600;700&display=swap">
<style>
:root{
  --orange:#E8694A;
  --orange-soft:#F4B9A8;
  --navy:#3B5681;
  --navy-dark:#2A3F63;
  --ink:#1C1C1C;
  --muted:#6E6E6E;
  --blush:#FCF1EE;
  --white:#FFFFFF;
  --line:#E6E6E6;
}
*{margin:0;padding:0;box-sizing:border-box}
html,body{width:1200px;height:3915px;overflow:hidden}
body{font-family:'Montserrat',sans-serif;color:var(--ink);background:var(--white);position:relative}
.abs{position:absolute}
.top-strip{position:absolute;left:0;top:0;width:1200px;height:12px;background:var(--orange)}

/* header */
.site-header{position:absolute;top:12px;left:0;width:1200px;height:113px;background:var(--white)}
.brand{position:absolute;left:71px;top:24px;display:flex;align-items:center;gap:14px}
.brand-mark{width:54px;height:54px;border:5px solid var(--orange);border-radius:50%}
.brand-name{font-weight:600;font-size:30px;line-height:31px;color:var(--navy)}
.main-nav a{position:absolute;top:47px;font-size:16px;color:#3a3a3a;text-decoration:none}
.main-nav a.active{color:var(--orange);text-decoration:underline;text-underline-offset:5px}
.btn{display:inline-flex;align-items:center;justify-content:center;background:var(--navy);color:var(--white);border-radius:6px;font-size:14px;font-weight:500;text-decoration:none}
.btn-start{position:absolute;left:1010px;top:38px;width:119px;height:37px}

/* hero */
.hero{position:absolute;top:125px;left:0;width:1200px;height:471px;background:linear-gradient(160deg,#26426E 0%,#3E5F8C 55%,#5876A0 100%)}
.hero-box{position:absolute;left:224px;top:99px;width:754px;height:200px;background:rgba(30,42,66,.72);border:4px solid #A9B3C2;text-align:center}
.hero-box h1{margin-top:36px;font-size:44px;font-weight:700;color:var(--orange)}
.hero-box p{margin:14px auto 0;width:660px;font-size:17px;line-height:26px;color:var(--white);font-weight:500}

/* about */
.about-ring{position:absolute;left:-130px;top:737px}
.photo{background:linear-gradient(150deg,#C9CFD3,#B07D5E 55%,#8A9AA0)}
.about-photo-main{position:absolute;left:113px;top:683px;width:342px;height:475px}
.about-photo-code{position:absolute;left:370px;top:837px;width:213px;height:261px;border:8px solid var(--white);background:linear-gradient(150deg,#2C3D4F,#10161F 60%,#3C5A66)}
.eyebrow{font-size:26px;color:var(--orange);font-weight:500}
.heading{font-size:36px;font-weight:500;line-height:42px;color:var(--ink)}
.about-text{position:absolute;left:642px;top:722px;width:480px}
.about-text .heading{margin-top:14px}
.about-text p{margin-top:28px;font-size:14px;line-height:23px;color:var(--muted)}
.feature{position:absolute;top:1050px;display:flex;gap:16px}
.icon-box{width:66px;height:66px;background:#FBE3DC;display:flex;align-items:center;justify-content:center}
.feature h4{font-size:15px;font-weight:500;color:var(--navy);margin-top:0}
.feature p{font-size:12px;line-height:18px;color:var(--muted);margin-top:6px;width:120px}

/* services */
.services{position:absolute;top:1247px;left:0;width:1200px;height:494px;background:var(--blush)}
.btn-small{position:absolute;height:33px;font-size:14px}
.service-card{position:absolute;top:199px;width:307px;height:210px;background:var(--white);box-shadow:0 2px 8px rgba(0,0,0,.06);padding:23px 17px}
.service-card.featured{background:linear-gradient(180deg,#4E5C80,#C9684E)}
.service-card .icon-box{background:#FBE3DC}
.service-card.featured .icon-box{background:var(--white)}
.service-card h3{margin-top:25px;font-size:17px;font-weight:500;color:var(--navy)}
.service-card.featured h3,.service-card.featured p{color:var(--white)}
.service-card p{margin-top:10px;font-size:13px;line-height:19px;color:var(--muted)}

/* cases */
.case-card{position:absolute;top:1944px;width:217px;height:234px;background:linear-gradient(160deg,#1F3347,#4C6478 60%,#2A3440)}
.case-card span{position:absolute;left:16px;bottom:24px;font-size:17px;font-weight:600;color:var(--white)}
.case-arrow{position:absolute;right:24px;bottom:18px;width:28px;height:28px;background:var(--orange);display:flex;align-items:center;justify-content:center}
.dots{position:absolute;display:flex;gap:10px;align-items:center}
.dots i{width:6px;height:6px;border-radius:50%;background:var(--navy);display:block}
.dots i.on{width:14px;height:14px;border:2px solid var(--navy);background:radial-gradient(var(--navy) 3px,transparent 4px)}

/* process */
.process{position:absolute;top:2315px;left:0;width:1200px;height:570px;background:var(--blush)}
.center{text-align:center;width:1200px;left:0}
.step{position:absolute;top:2528px;width:300px;text-align:center}
.step-circle{position:relative;margin:0 auto;width:152px;height:152px;border:1.5px dashed var(--orange);border-radius:50%;display:flex;align-items:center;justify-content:center}
.step-circle .core{width:130px;height:130px;border-radius:50%;background:var(--navy);display:flex;align-items:center;justify-content:center}
.step-num{position:absolute;left:0;top:0;width:28px;height:28px;border-radius:50%;background:#7A4A4F;color:var(--white);font-size:14px;display:flex;align-items:center;justify-content:center}
.step h3{margin-top:30px;font-size:19px;font-weight:500}
.step p{margin-top:14px;font-size:13px;line-height:22px;color:var(--muted)}

/* blog */
.post{position:absolute;top:3098px;width:299px;height:365px;background:var(--white);box-shadow:0 2px 10px rgba(0,0,0,.08)}
.post-img{height:203px;background:linear-gradient(150deg,#5A6F80,#AFB8BE 50%,#34414F)}
.post-meta{margin:18px 17px 0;padding-bottom:12px;border-bottom:1px solid var(--line);font-size:10px;color:var(--muted);display:flex;gap:14px}
.post-meta b{color:var(--orange);font-weight:400}
.post h3{margin:22px 17px 0;font-size:16px;line-height:23px;font-weight:500}
.post a{display:block;margin:12px 17px 0;font-size:13px;color:var(--navy)}

/* footer */
.site-footer{position:absolute;top:3600px;left:0;width:1200px;height:315px;background:var(--navy);overflow:hidden;color:var(--white)}
.footer-brand{position:absolute;left:113px;top:50px;display:flex;align-items:center;gap:14px}
.footer-brand .brand-mark{border-color:var(--white);width:52px;height:52px}
.footer-brand .brand-name{color:var(--white);font-size:28px;line-height:30px}
.footer-about{position:absolute;left:113px;top:138px;width:260px;font-size:13px;line-height:21px}
.social{position:absolute;left:113px;top:211px;display:flex;gap:6px}
.social i{width:22px;height:22px;border:1.5px solid var(--white);border-radius:50%;display:block}
.footer-col{position:absolute;top:50px}
.footer-col h4{font-size:19px;font-weight:600}
.footer-col ul{list-style:none;margin-top:16px}
.footer-col li{font-size:14px;line-height:28.5px}
.footer-col li::before{content:"»";margin-right:8px;font-weight:700}
.footer-rule{position:absolute;left:0;top:259px;width:1200px;height:1px;background:rgba(255,255,255,.35)}
.copyright{position:absolute;top:276px;width:1200px;text-align:center;font-size:13px}
</style>
</head>
<body>
<div class="top-strip"></div>

<header class="site-header">
  <div class="brand"><span class="brand-mark"></span><div class="brand-name">QR.KA<br>Horizon</div></div>
  <nav class="main-nav">
    <a href="#" class="active" style="left:443px">Home</a>
    <a href="#" style="left:527px">Solutions</a>
    <a href="#" style="left:636px">Who Are We</a>
    <a href="#" style="left:769px">Testimonial</a>
    <a href="#" style="left:895px">Contact Us</a>
  </nav>
  <a href="#" class="btn btn-start">Get Started</a>
</header>

<section class="hero" role="img" aria-label="Blurred background of flowing binary code in deep blue">
  <div class="hero-box">
    <h1>WELCOME TO QR.KA Horizon</h1>
    <p>Lorem ipsum dolor sit amet, consectetur adipiscing elit, sed do eiusmod tempor incididunt ut labore et dolore magna aliqua.</p>
  </div>
</section>

<svg class="about-ring" width="250" height="370" viewBox="0 0 250 370" aria-hidden="true">
  <defs><linearGradient id="ringGrad" x1="0" y1="0" x2="0" y2="1"><stop offset="0" stop-color="#4E5C80"/><stop offset="1" stop-color="#D9684C"/></linearGradient></defs>
  <path d="M245 30 A155 155 0 1 0 245 340" fill="none" stroke="url(#ringGrad)" stroke-width="36"/>
</svg>
<div class="about-photo-main photo" role="img" aria-label="Smiling professional holding a tablet in a bright office"></div>
<div class="about-photo-code" role="img" aria-label="Developer working on code in a dark room"></div>

<div class="about-text">
  <div class="eyebrow">About Us</div>
  <h2 class="heading">We Strive to Offer<br>Intelligent Business<br>Solutions</h2>
  <p>Lorem ipsum dolor sit amet, consectetur adipiscing elit, sed do eiusmod tempor incididunt ut labore et dolore magna aliqua. Quis ipsum suspendisse ultrices gravida. Risus commodo viverra maecenas accumsan lacus vel facilisis.</p>
</div>
<div class="feature" style="left:642px">
  <div class="icon-box"><svg width="40" height="36" viewBox="0 0 40 36" fill="none" stroke="#E8694A" stroke-width="1.6"><rect x="3" y="6" width="34" height="20"/><path d="M14 32h12M20 26v6M10 14h20M10 19h12"/></svg></div>
  <div><h4>Best Services</h4><p>Lorem ipsum dolor sit amet,</p></div>
</div>
<div class="feature" style="left:885px">
  <div class="icon-box"><svg width="38" height="38" viewBox="0 0 38 38" fill="none" stroke="#E8694A" stroke-width="1.6"><circle cx="19" cy="19" r="14"/><text x="19" y="23" font-size="9" text-anchor="middle" fill="#E8694A" stroke="none" font-family="Montserrat,sans-serif">24/7</text></svg></div>
  <div><h4>24/7 Call Support</h4><p>Lorem ipsum dolor sit amet,</p></div>
</div>

<section class="services">
  <div class="abs eyebrow" style="left:111px;top:78px">What We Offer</div>
  <h2 class="abs heading" style="left:111px;top:118px">Excellent It Services</h2>
  <a href="#" class="btn btn-small" style="left:938px;top:103px;width:150px">View All Services</a>
  <div class="service-card" style="left:111px">
    <div class="icon-box"><svg width="40" height="36" viewBox="0 0 40 36" fill="none" stroke="#E8694A" stroke-width="1.6"><rect x="3" y="6" width="34" height="20"/><path d="M14 32h12M20 26v6M10 14h20M10 19h12"/></svg></div>
    <h3>IT Management</h3>
    <p>Lorem ipsum dolor sit amet, conse ctetur adipiscing elit, sed do eiusmod tempor in ut labore et dolore magna aliqua.</p>
  </div>
  <div class="service-card featured" style="left:446px">
    <div class="icon-box"><svg width="40" height="36" viewBox="0 0 40 36" fill="none" stroke="#E8694A" stroke-width="1.6"><rect x="3" y="6" width="34" height="20"/><path d="M14 32h12M20 26v6M10 14h20M10 19h12"/></svg></div>
    <h3>Software Development</h3>
    <p>Lorem ipsum dolor sit amet, conse ctetur adipiscing elit, sed do eiusmod tempor in ut labore et dolore magna aliqua.</p>
  </div>
  <div class="service-card" style="left:780px">
    <div class="icon-box"><svg width="40" height="36" viewBox="0 0 40 36" fill="none" stroke="#E8694A" stroke-width="1.6"><rect x="3" y="6" width="34" height="20"/><path d="M14 32h12M20 26v6M10 14h20M10 19h12"/></svg></div>
    <h3>Integration Services</h3>
    <p>Lorem ipsum dolor sit amet, conse ctetur adipiscing elit, sed do eiusmod tempor in ut labore et dolore magna aliqua.</p>
  </div>
</section>

<div class="abs eyebrow" style="left:111px;top:1822px">From Our Case Studies</div>
<h2 class="abs heading" style="left:111px;top:1862px">We Delivered Best Solution</h2>
<a href="#" class="btn btn-small" style="left:964px;top:1848px;width:124px">View All Case</a>
<div class="case-card" style="left:246px" role="img" aria-label="Engineer with laptop in a server room"><span>IT Management</span><div class="case-arrow"><svg width="16" height="14" viewBox="0 0 16 14" fill="none" stroke="#fff" stroke-width="2"><path d="M1 7h13M8 1l6 6-6 6"/></svg></div></div>
<div class="case-card" style="left:491px" role="img" aria-label="Developer coding at a workstation"><span>Platform Integration</span></div>
<div class="case-card" style="left:738px" role="img" aria-label="Two colleagues reviewing a tablet in a data center"><span>Network Security</span></div>
<div class="case-card" style="left:983px" role="img" aria-label="Team collaborating around a laptop"><span>Product Design</span></div>
<div class="dots" style="left:554px;top:2215px"><i></i><i class="on"></i><i></i><i></i><i></i><i></i></div>

<section class="process">
  <div class="abs center eyebrow" style="top:80px">Work Process</div>
  <h2 class="abs center heading" style="top:120px">Our Development Process</h2>
  <svg class="abs" style="left:388px;top:290px" width="90" height="95" viewBox="0 0 90 95" fill="none" stroke="#F7D9CF" stroke-width="10" stroke-linecap="round"><path d="M8 88 C10 45 40 25 75 22"/><path d="M58 8 L80 22 L62 38"/></svg>
  <svg class="abs" style="left:738px;top:290px" width="90" height="95" viewBox="0 0 90 95" fill="none" stroke="#F7D9CF" stroke-width="10" stroke-linecap="round"><path d="M8 88 C10 45 40 25 75 22"/><path d="M58 8 L80 22 L62 38"/></svg>
</section>

<div class="step" style="left:102px">
  <div class="step-circle"><span class="step-num">1</span><div class="core"><svg width="64" height="64" viewBox="0 0 64 64" fill="none" stroke="#fff" stroke-width="2"><rect x="14" y="10" width="36" height="46" rx="4"/><path d="M22 24l3 3 5-6M34 24h10M22 36l3 3 5-6M34 36h10M22 48h22"/></svg></div></div>
  <h3>Define Requirements</h3>
  <p>Lorem ipsum dolor sit amet,<br>adipiscing elit, sed do eiusmod tempor<br>incididunt ut labore et</p>
</div>
<div class="step" style="left:454px">
  <div class="step-circle"><span class="step-num">2</span><div class="core"><svg width="64" height="64" viewBox="0 0 64 64" fill="none" stroke="#fff" stroke-width="2"><rect x="10" y="10" width="18" height="30" rx="2"/><rect x="30" y="20" width="14" height="28" rx="2"/><rect x="46" y="30" width="10" height="20" rx="2"/><path d="M14 18h10M14 26h10M34 28h6M34 36h6M19 40v14"/></svg></div></div>
  <h3>Design &amp; Prototyping</h3>
  <p>Lorem ipsum dolor sit amet,<br>adipiscing elit, sed do eiusmod tempor<br>incididunt ut labore et</p>
</div>
<div class="step" style="left:805px">
  <div class="step-circle"><span class="step-num">3</span><div class="core"><svg width="64" height="64" viewBox="0 0 64 64" fill="none" stroke="#fff" stroke-width="2"><path d="M18 14h22l8 8v32H18z"/><path d="M40 14v8h8M24 30h18M24 38h18M24 46h10"/><circle cx="46" cy="46" r="7"/><path d="M43 46l2 2 4-4"/></svg></div></div>
  <h3>Final Solution</h3>
  <p>Lorem ipsum dolor sit amet,<br>adipiscing elit, sed do eiusmod tempor<br>incididunt ut labore et</p>
</div>

<div class="abs center eyebrow" style="top:2968px">Blog &amp; News</div>
<h2 class="abs center heading" style="top:3006px">Explore Blogs and News</h2>
<article class="post" style="left:111px">
  <div class="post-img" role="img" aria-label="Team of colleagues gathered around a computer"></div>
  <div class="post-meta"><span><b>●</b> By Admin</span><span><b>○</b> 0 Comments</span></div>
  <h3>Lorem ipsum dolor sit amet, co sectetur adipi</h3><a href="#">Read More</a>
</article>
<article class="post" style="left:450px">
  <div class="post-img" role="img" aria-label="Developer writing code on multiple screens"></div>
  <div class="post-meta"><span><b>●</b> By Admin</span><span><b>○</b> 0 Comments</span></div>
  <h3>Lorem ipsum dolor sit amet, co sectetur adipi</h3><a href="#">Read More</a>
</article>
<article class="post" style="left:790px">
  <div class="post-img" role="img" aria-label="Technician with a tablet in a server aisle"></div>
  <div class="post-meta"><span><b>●</b> By Admin</span><span><b>○</b> 0 Comments</span></div>
  <h3>Lorem ipsum dolor sit amet, co sectetur adipi</h3><a href="#">Read More</a>
</article>
<div class="dots" style="left:554px;top:3500px"><i></i><i class="on"></i><i></i><i></i><i></i><i></i></div>

<footer class="site-footer">
  <svg class="abs" style="left:0;top:0" width="80" height="160" viewBox="0 0 80 160"><path d="M0 0h40l35 45L0 150z" fill="#E8694A"/></svg>
  <svg class="abs" style="right:0;top:140px" width="70" height="175" viewBox="0 0 70 175"><path d="M70 0v175H50L10 105z" fill="#E8694A"/></svg>
  <div class="footer-brand"><span class="brand-mark"></span><div class="brand-name">QR.KA<br>Horizon</div></div>
  <p class="footer-about">Lorem ipsum dolor sit amet, consec tetur adipiscing elit, sed do eiusmod tempor incididunt ut</p>
  <div class="social"><i></i><i></i><i></i><i></i><i></i></div>
  <div class="footer-col" style="left:462px"><h4>IT Solution</h4><ul><li>IT Management</li><li>SEO Optimization</li><li>Web Development</li><li>Cyber Security</li><li>Data Security</li></ul></div>
  <div class="footer-col" style="left:724px"><h4>Quick Link</h4><ul><li>About Us</li><li>Our Services</li><li>Pricing Plan</li><li>Our Projects</li><li>Our Team</li></ul></div>
  <div class="footer-col" style="left:940px"><h4>Legal Policy</h4><ul><li>Terms Of Services</li><li>Privacy Policy</li><li>Cookies Policy</li><li>FAQs</li><li>Sitemaps</li></ul></div>
  <div class="footer-rule"></div>
  <div class="copyright">Copyright © 2025 QR.KA Horizon. All rights reserved.</div>
</footer>
</body>
</html>
```